Bright Towns Forum PowerPoint Design Template and Sample Deck

The Bright Towns Forum is an international organization that seeks to improve the livability, workability and sustainability of the world’s cities.
We seek a versatile PowerPoint design template with 10 slide types plus a “self-documenting” sample deck. Your design will be used in keynote speeches and workshops around the world.
After the contest is completed, we will ask the winning designer to add 10-20 additional slide types for $75 per slide. We also seek a long-term relationship whereby we can request “custom” slides and/or ask the designer to touch up the slides we build to make them better.
FILES. We have uploaded several files:
2. PALETTE. Shows our official colors.
3 LOGOS. Several individual files with different variations of our logo. Some with our motto, some without.
2. SAMPLE SLIDES. Because we were unable to successfully upload our sample deck, we are making it available via this FileNook link:
https://www.filenook-example.com/s/k7qrtmzp2wd9hxa/The%20Bright%20Towns%20Forum%20Design%20Contest%20Notes.docx?dl=0
Target Market(s)
Mayors, department heads, CIOs, senior executives from technology companies
Industry/Entity Type
Information Technology
Colors
Designer to choose colors to be used in the design.
Requirements
Must have
- Please see uploaded Word document for requirements, nice to haves and should not haves and uploaded palette for color preferences.
Nice to have
- see above
Should not have
- see above

```html
<!DOCTYPE html>
<html lang="en">
<head>
<meta charset="utf-8">
<title>Bright Towns Forum – Title Slide</title>
<link href="https://fonts.googleapis.com/css2?family=Arimo:wght@400;700&display=swap" rel="stylesheet">
<style>
  :root {
    --navy-deep: #1d3a5c;
    --navy-mid: #3d5f82;
    --slate-light: #7e95ae;
    --white: #ffffff;
    --accent-orange: #f7941d;
  }
  html, body {
    margin: 0;
    padding: 0;
    width: 1200px;
    height: 675px;
    overflow: hidden;
    background: var(--navy-deep);
  }
  .slide {
    position: relative;
    width: 1200px;
    height: 675px;
    overflow: hidden;
    font-family: "Arimo", Arial, sans-serif;
  }
  .slide-backdrop {
    position: absolute;
    inset: 0;
    background:
      radial-gradient(ellipse at 55% 40%, rgba(126,149,174,0.55) 0%, rgba(126,149,174,0) 60%),
      radial-gradient(ellipse at 85% 15%, rgba(150,170,195,0.45) 0%, rgba(150,170,195,0) 45%),
      linear-gradient(90deg, rgba(20,45,75,0.45) 0%, rgba(20,45,75,0) 30%),
      linear-gradient(180deg, var(--navy-mid) 0%, #2f4f72 55%, var(--navy-deep) 100%);
  }
  .slide-content {
    position: absolute;
    inset: 0;
    text-align: center;
  }
  .brand {
    position: absolute;
    top: 124px;
    left: 0;
    right: 0;
    display: flex;
    justify-content: center;
    align-items: center;
    gap: 14px;
  }
  .brand-square {
    width: 22px;
    height: 22px;
    background: var(--accent-orange);
  }
  .brand-name {
    margin: 0;
    color: var(--white);
    font-weight: 700;
    font-size: 30px;
    line-height: 1;
    letter-spacing: 3px;
  }
  .slide-title {
    position: absolute;
    top: 277px;
    left: 0;
    right: 0;
    margin: 0;
    color: var(--white);
    font-weight: 700;
    font-size: 67px;
    line-height: 1;
  }
  .slide-subtitle {
    position: absolute;
    top: 391px;
    left: 0;
    right: 0;
    margin: 0;
    color: var(--accent-orange);
    font-weight: 700;
    font-size: 44px;
    line-height: 1;
  }
</style>
</head>
<body>
  <div class="slide">
    <div class="slide-backdrop" role="img" aria-label="Blue-tinted photo of a business handshake over a desk with a laptop, overlaid with a faint world map"></div>
    <div class="slide-content">
      <div class="brand">
        <span class="brand-square"></span>
        <p class="brand-name">BRIGHT TOWNS FORUM</p>
      </div>
      <h1 class="slide-title">TITLE FOR THE SLIDE</h1>
      <h2 class="slide-subtitle">SUB TITLE FOR THE SLIDE</h2>
    </div>
  </div>
</body>
</html>
```